We are a recruitment company based in Norwich/Cambridge England.
I have included our company logo which we want to remain the same.

What we are looking for is a new creative Business card which will really stand out!!

Contact Information for Business Card

Harriet Dunmore
email: Harriet@plavex.co.uk
Address: Brackwell House
Fenmoor Enterprise Park
Partridge Way
Norwich
QB9 3KX
Tel:01632 960418

```html
<!DOCTYPE html>
<html lang="en">
<head>
<meta charset="utf-8">
<title>Plavex Business Card</title>
<link rel="stylesheet" href="https://fonts.googleapis.com/css2?family=Arimo:wght@400;700&display=swap">
<style>
  :root {
    --page-bg: #d9d4cd;
    --card-light: #f1efec;
    --card-mid: #dedbd7;
    --brand-green: #4c9a2a;
    --brand-grey: #55525a;
    --band-dark: #4a4347;
    --text-light: #e4e1df;
    --text-soft: #d2ccd0;
  }
  html, body {
    margin: 0;
    padding: 0;
    width: 1200px;
    height: 970px;
    overflow: hidden;
    background: var(--page-bg);
    font-family: "Arimo", Arial, sans-serif;
  }
  .business-card {
    position: absolute;
    left: 80px;
    top: 189px;
    width: 1040px;
    height: 592px;
    overflow: hidden;
    background: linear-gradient(160deg, var(--card-light) 0%, var(--card-mid) 100%);
    box-shadow: 0 10px 30px rgba(0,0,0,0.18);
  }
  .brand-lockup {
    position: absolute;
    left: 52px;
    top: 118px;
  }
  .brand-name {
    display: flex;
    align-items: center;
    gap: 18px;
    font-size: 76px;
    font-weight: 700;
    color: var(--brand-green);
    line-height: 1;
    letter-spacing: -1px;
  }
  .brand-dot {
    width: 58px;
    height: 58px;
    border-radius: 50%;
    background: var(--brand-grey);
  }
  .brand-tagline {
    margin: 12px 0 0 78px;
    font-size: 15px;
    font-weight: 700;
    letter-spacing: 4.6px;
    color: var(--brand-grey);
  }
  .name-band {
    position: absolute;
    left: 0;
    top: 303px;
    width: 582px;
    height: 56px;
    background: var(--brand-green);
    display: flex;
    align-items: center;
    padding-left: 50px;
    box-sizing: border-box;
    color: var(--text-light);
  }
  .person-name {
    font-size: 33px;
    font-weight: 700;
  }
  .band-divider {
    width: 2px;
    height: 38px;
    background: var(--text-light);
    margin: 0 22px 0 26px;
  }
  .person-role {
    font-size: 26px;
  }
  .contact-band {
    position: absolute;
    left: 0;
    top: 362px;
    width: 720px;
    height: 230px;
    background: linear-gradient(90deg, var(--band-dark) 0%, var(--band-dark) 62%, rgba(74,67,71,0) 100%);
    color: var(--text-soft);
  }
  .address {
    position: absolute;
    left: 50px;
    top: 22px;
    font-size: 25px;
    line-height: 33px;
  }
  .contact-list {
    position: absolute;
    left: 48px;
    top: 96px;
    margin: 0;
    padding: 0;
    list-style: none;
    font-size: 25px;
  }
  .contact-item {
    display: flex;
    align-items: center;
    height: 35px;
  }
  .contact-icon {
    width: 30px;
    height: 30px;
    margin-right: 22px;
  }
  .symbol-area {
    position: absolute;
    right: 0;
    top: 0;
    width: 430px;
    height: 592px;
    background: radial-gradient(circle at 75% 60%, rgba(76,154,42,0.35) 0%, rgba(74,67,71,0.55) 45%, rgba(74,67,71,0.15) 80%, rgba(74,67,71,0) 100%);
  }
</style>
</head>
<body>
  <main class="business-card">
    <div class="brand-lockup">
      <div class="brand-name"><span class="brand-dot"></span>Plavex</div>
      <div class="brand-tagline">Technology Recruitment</div>
    </div>

    <div class="symbol-area" role="img" aria-label="Large brand symbol decoration in grey and green"></div>

    <div class="name-band">
      <span class="person-name">Harriet Dunmore</span>
      <span class="band-divider"></span>
      <span class="person-role">CEO</span>
    </div>

    <section class="contact-band">
      <div class="address">Brackwell House, Partridge Way<br>Fenmoor Enterprise Park, Norwich</div>
      <ul class="contact-list">
        <li class="contact-item">
          <svg class="contact-icon" viewBox="0 0 30 30" aria-hidden="true">
            <circle cx="15" cy="15" r="13" fill="none" stroke="currentColor" stroke-width="1.6"/>
            <rect x="10.5" y="7.5" width="9" height="15" rx="1.5" fill="none" stroke="currentColor" stroke-width="1.6"/>
            <circle cx="15" cy="19.5" r="0.9" fill="currentColor"/>
          </svg>01632 960418
        </li>
        <li class="contact-item">
          <svg class="contact-icon" viewBox="0 0 30 30" aria-hidden="true">
            <circle cx="15" cy="15" r="13" fill="none" stroke="currentColor" stroke-width="1.6"/>
            <rect x="8" y="10" width="14" height="10" fill="none" stroke="currentColor" stroke-width="1.6"/>
            <path d="M8 10 L15 16 L22 10" fill="none" stroke="currentColor" stroke-width="1.6"/>
          </svg>Harriet@plavex.co.uk
        </li>
        <li class="contact-item">
          <svg class="contact-icon" viewBox="0 0 30 30" aria-hidden="true">
            <circle cx="15" cy="15" r="13" fill="none" stroke="currentColor" stroke-width="1.6"/>
            <circle cx="15" cy="15" r="8" fill="none" stroke="currentColor" stroke-width="1.4"/>
            <ellipse cx="15" cy="15" rx="3.5" ry="8" fill="none" stroke="currentColor" stroke-width="1.2"/>
            <path d="M7 15 H23" stroke="currentColor" stroke-width="1.2"/>
          </svg>www.plavex.co.uk
        </li>
      </ul>
    </section>
  </main>
</body>
</html>
```